PHGCCUL re-branding website and logo

We are looking for a new webpage design and logo our current page address is www.phgccul-example.org. We want to create a new design using PHGCCUL Pinewood and Harbour Growers Co-operative Credit Union limited and another with the purposed new name PHFC Pinewood and Harbour Financial Co-operative, the color scheme is purple and burnt orange. Our new logo and webpage should communicate change and growth purposed theme continuing our legacy here to server past, present and future generations. Our idea for the logo is a live shot of hands of different ages in a circle holding a tree

Target Market(s)

Everyone

Contact Information for Business Card

Company Name
Telephone number
Address
slot to enter employee info

Logo Text

(P & H) Pinewood And Harbour Financial Co-operative

Coding

Coded - Design and coding required

Number of Pages Required

2 page

Colors
f37122
fbed22
6b449b

Requirements
Must have
• links for social media

```html
<!DOCTYPE html>
<html lang="en">
<head>
<meta charset="utf-8">
<title>PHFC – Pinewood and Harbour Financial Co-operative</title>
<link href="https://fonts.googleapis.com/css2?family=Lato:wght@400;700;900&family=Open+Sans:wght@400;600;700&display=swap" rel="stylesheet">
<style>
:root{
  --orange:#f37122;
  --olive:#cbc62b;
  --purple:#6b449b;
  --ink:#222222;
  --text:#555555;
  --muted:#777777;
  --panel:rgba(58,58,58,.92);
  --band:#f2f5f4;
  --white:#ffffff;
  --line:#dddddd;
}
*{margin:0;padding:0;box-sizing:border-box}
html,body{width:1200px;height:2808px;overflow:hidden}
body{position:relative;background:var(--white);font-family:"Open Sans",Arial,sans-serif;color:var(--text)}
.abs{position:absolute}
a{color:inherit;text-decoration:none}

/* hero */
.hero{left:0;top:0;width:1200px;height:550px;background:linear-gradient(180deg,#3f78a8 0%,#7fb0cf 30%,#2aa3b4 48%,#1c7f8a 62%,#4d6a3a 78%,#2f4a2a 100%)}
.hero-shade{left:0;top:0;width:1200px;height:550px;background:linear-gradient(180deg,rgba(0,0,0,.35),rgba(0,0,0,0) 30%,rgba(0,0,0,0) 80%,rgba(0,0,0,.15))}
.brand{left:100px;top:12px;display:flex;align-items:center;gap:14px}
.brand-mark{width:84px;height:84px;border-radius:50%;background:#7a6a4a;border:2px solid rgba(255,255,255,.7)}
.brand-name{font-family:"Lato",sans-serif;font-weight:900;font-size:44px;color:var(--white);letter-spacing:1px}
.topbar{right:96px;top:18px;display:flex;align-items:center;gap:24px;font-size:15px;font-weight:600;color:var(--white)}
.topbar .item{display:flex;align-items:center;gap:12px}
.ring{width:34px;height:34px;border-radius:50%;border:1.5px solid rgba(255,255,255,.8);display:flex;align-items:center;justify-content:center}
.login{border:1.5px solid rgba(255,255,255,.85);border-radius:18px;padding:6px 16px;font-size:13px;font-weight:700;display:flex;gap:8px;align-items:center}
.nav{right:96px;top:74px;display:flex;gap:30px;font-size:15px;font-weight:700;color:var(--white);align-items:center}
.nav .active{color:var(--orange)}
.hero-title{left:0;width:1200px;text-align:center;color:var(--white);font-family:"Lato",sans-serif;text-shadow:0 2px 6px rgba(0,0,0,.35)}
.hero-title.small{top:206px;font-size:38px;font-weight:700;letter-spacing:.5px}
.hero-title.big{top:256px;font-size:56px;font-weight:900;letter-spacing:1px}
.dots{left:560px;top:488px;display:flex;gap:8px}
.dots span{width:15px;height:15px;border-radius:50%;border:2px solid var(--white)}
.dots .on{background:var(--purple)}

/* welcome */
.section-title{left:0;width:1200px;text-align:center;font-family:"Lato",sans-serif;font-weight:900;font-size:31px;color:var(--ink)}
.welcome-title{top:610px}
.lead{left:290px;top:668px;width:620px;text-align:center;font-size:12.5px;line-height:24px;color:var(--muted)}
.card{top:745px;width:303px;height:313px;color:var(--white);text-align:center;box-shadow:0 4px 6px rgba(0,0,0,.12)}
.card svg.shape{position:absolute;left:0;top:0}
.card .icon{position:absolute;left:121px;top:34px;width:60px;height:60px}
.card h3{position:absolute;top:148px;width:100%;font-size:19px;font-weight:700}
.card p{position:absolute;top:186px;left:30px;width:243px;font-size:12.5px;line-height:22px}
.card .btn{position:absolute;left:76px;top:247px;width:151px;height:32px;border:1.5px solid var(--white);border-radius:16px;font-size:12px;font-weight:700;line-height:29px}
.c1{left:100px}.c2{left:448px}.c3{left:797px}

/* tools */
.tools-photo{left:509px;top:1133px;width:691px;height:473px;background:linear-gradient(135deg,#e9e6e1 0%,#c8c3bc 45%,#9da0a6 75%,#d8d6d2 100%)}
.tools-panel{left:0;top:1133px;width:509px;height:473px;background:linear-gradient(135deg,#4b4b4b,#3a3a3a)}
.tools-title{left:100px;top:1168px;font-family:"Lato",sans-serif;font-weight:700;font-size:27px;color:var(--white)}
.tool{left:98px;display:flex;align-items:center;gap:28px;color:var(--white);font-size:19px;font-weight:600}
.tool .ring{width:76px;height:76px;border:2px solid rgba(255,255,255,.75)}

/* products */
.products-title{top:1672px}
.product{top:1748px;width:316px}
.product .photo{width:316px;height:218px}
.product h4{margin-top:40px;font-family:"Lato",sans-serif;font-weight:900;font-size:18px;color:var(--ink)}
.product p{margin-top:12px;font-size:12.5px;line-height:24px;color:var(--muted)}
.more{display:inline-block;margin-top:14px;border:1.5px solid var(--line);border-radius:16px;padding:5px 13px;font-size:12px;font-weight:700;color:var(--orange)}

/* news & rates */
.news-band{left:0;top:2218px;width:814px;height:322px;background:var(--band)}
.news-photo{left:100px;top:2276px;width:227px;height:206px;border:5px solid var(--white);box-shadow:0 1px 4px rgba(0,0,0,.2);background:linear-gradient(135deg,#d8d2c8,#8a7c6e 55%,#3b4a6a)}
.news-title{left:372px;top:2267px;font-family:"Lato",sans-serif;font-weight:900;font-size:29px;color:var(--ink)}
.news-head{left:372px;top:2314px;font-size:20px;font-weight:600;color:var(--ink)}
.news-meta{left:372px;top:2354px;font-size:12px;color:var(--muted);display:flex;gap:8px;align-items:center}
.news-meta .sep{color:#aaa}
.news-text{left:372px;top:2386px;width:440px;font-size:12.5px;line-height:24px;color:var(--muted)}
.news-more{left:372px;top:2458px;font-size:13px;font-weight:700;color:var(--orange)}
.arrows{left:689px;top:2456px;display:flex;gap:8px}
.arrows span{width:24px;height:24px;border-radius:50%;background:#bbb;display:flex;align-items:center;justify-content:center}
.rates{left:814px;top:2218px;width:386px;height:322px;background:var(--purple);color:var(--white)}
.rates h2{position:absolute;left:41px;top:28px;font-family:"Lato",sans-serif;font-weight:700;font-size:30px}
.rate{position:absolute;left:41px;width:330px;font-size:14px}
.rate b{position:absolute;left:184px;top:-3px;font-size:18px;font-weight:700}
.rate b small{font-size:13px;font-weight:400}
.rates .note{position:absolute;left:41px;top:262px;font-size:11.5px}
.rates .note strong{margin-left:10px;font-size:12.5px}

/* footer */
.contacts{left:0;top:2606px;width:1200px;display:flex;justify-content:center;gap:68px;font-size:16px;color:#444}
.contacts .item{display:flex;align-items:center;gap:22px}
.contacts .ring{width:42px;height:42px;border:1.5px solid #999}
.footer-nav{left:0;top:2670px;width:1200px;text-align:center;font-size:15.5px;color:#333}
.footer-nav span{margin:0 12px;color:#666}
.rule{left:100px;top:2720px;width:1001px;height:1px;background:var(--line)}
.copyright{left:100px;top:2752px;font-size:12.5px;color:var(--muted)}
.social{left:977px;top:2751px;display:flex;gap:9px}
.social span{width:25px;height:25px;border-radius:50%;border:1.5px solid var(--orange)}
</style>
</head>
<body>

<!-- hero -->
<div class="abs hero" role="img" aria-label="Aerial photograph of a tropical island coastline with turquoise sea and resort buildings"></div>
<div class="abs hero-shade"></div>

<div class="abs brand">
  <div class="brand-mark"></div>
  <div class="brand-name">P &amp; H</div>
</div>

<div class="abs topbar">
  <div class="item"><span class="ring"><svg width="16" height="16" viewBox="0 0 24 24"><path fill="#f37122" d="M6.6 10.8a15 15 0 006.6 6.6l2.2-2.2c.3-.3.7-.4 1-.2 1.1.4 2.3.6 3.6.6.6 0 1 .4 1 1V20c0 .6-.4 1-1 1A17 17 0 013 4c0-.6.4-1 1-1h3.5c.6 0 1 .4 1 1 0 1.3.2 2.5.6 3.6.1.3 0 .7-.2 1z"/></svg></span>(555) 310-4827</div>
  <div class="item"><span class="ring"><svg width="16" height="16" viewBox="0 0 24 24"><path fill="#f37122" d="M4 8h16v9h-3v4H7v-4H4zM7 3h10v4H7zm2 12v4h6v-4z"/></svg></span>(555) 310-6158</div>
  <div class="login"><svg width="12" height="14" viewBox="0 0 12 14"><path fill="#f37122" d="M2 6V4a4 4 0 018 0v2h1v8H1V6zm2 0h4V4a2 2 0 00-4 0z"/></svg>INTERNET TELLER LOGIN</div>
</div>

<nav class="abs nav">
  <a class="active">HOME</a><a>ABOUT US</a><a>PRODUCT &amp; SERVICES</a><a>TOOLS &amp; BENEFITS</a><a>NEWS</a><a>CONTACT US</a>
  <svg width="16" height="16" viewBox="0 0 16 16"><circle cx="6.5" cy="6.5" r="5" fill="none" stroke="#fff" stroke-width="2.2"/><path d="M10.5 10.5L15 15" stroke="#fff" stroke-width="2.4"/></svg>
</nav>

<div class="abs hero-title small">PINEWOOD AND HARBOUR</div>
<div class="abs hero-title big">FINANCIAL CO-OPERATIVE</div>
<div class="abs dots"><span class="on"></span><span></span><span></span><span></span></div>

<!-- welcome -->
<h1 class="abs section-title welcome-title">WELCOME TO PHFC</h1>
<p class="abs lead">At Pinewood &amp; Harbour Growers Cooperative Credit Union Limited we focus on building relationships with our members that last. No hard sell, no hidden fees -- just good service and good advice.</p>

<div class="abs card c1">
  <svg class="shape" width="303" height="313"><path d="M0 79L100 40H203L303 79V313H0Z" fill="#f37122"/><circle cx="151.5" cy="64" r="59" fill="#fff" stroke="#f37122" stroke-width="6"/></svg>
  <svg class="icon" viewBox="0 0 60 60"><g fill="#f37122"><circle cx="30" cy="20" r="8"/><circle cx="15" cy="25" r="6"/><circle cx="45" cy="25" r="6"/><path d="M18 46c0-8 5-14 12-14s12 6 12 14z"/><path d="M5 46c0-7 4-12 10-12 2 0 4 .5 5 1.5-3 3-4 6-4 10.5z"/><path d="M55 46c0-7-4-12-10-12-2 0-4 .5-5 1.5 3 3 4 6 4 10.5z"/></g></svg>
  <h3>Memberships</h3>
  <p>The principle upon which the credit union was built revolutionized Banking</p>
  <div class="btn">BECOME A MEMBER</div>
</div>

<div class="abs card c2">
  <svg class="shape" width="303" height="313"><path d="M0 79L100 40H203L303 79V313H0Z" fill="#cbc62b"/><circle cx="151.5" cy="64" r="59" fill="#fff" stroke="#cbc62b" stroke-width="6"/></svg>
  <svg class="icon" viewBox="0 0 60 60"><rect x="14" y="6" width="32" height="48" rx="4" fill="#cbc62b"/><rect x="19" y="11" width="22" height="9" fill="#fff"/><g fill="#fff"><rect x="19" y="25" width="5" height="5"/><rect x="27.5" y="25" width="5" height="5"/><rect x="36" y="25" width="5" height="5"/><rect x="19" y="33" width="5" height="5"/><rect x="27.5" y="33" width="5" height="5"/><rect x="36" y="33" width="5" height="5"/><rect x="19" y="41" width="5" height="5"/><rect x="27.5" y="41" width="5" height="5"/><rect x="36" y="41" width="5" height="5"/></g></svg>
  <h3>Financial Calculators</h3>
  <p>The principle upon which the credit union was built revolutionized Banking</p>
  <div class="btn">CALCULATE NOW!</div>
</div>

<div class="abs card c3">
  <svg class="shape" width="303" height="313"><path d="M0 79L100 40H203L303 79V313H0Z" fill="#6b449b"/><circle cx="151.5" cy="64" r="59" fill="#fff" stroke="#6b449b" stroke-width="6"/></svg>
  <svg class="icon" viewBox="0 0 60 60"><path d="M34 14H12a4 4 0 00-4 4v28a4 4 0 004 4h28a4 4 0 004-4V28" fill="none" stroke="#6b449b" stroke-width="4"/><path d="M24 38l2-9L45 10l7 7-19 19z" fill="#6b449b"/></svg>
  <h3>Apply For A Loan</h3>
  <p>The principle upon which the credit union was built revolutionized Banking</p>
  <div class="btn">APPLY NOW!</div>
</div>

<!-- tools & benefits -->
<div class="abs tools-photo" role="img" aria-label="Photograph of a hand typing on a calculator beside a laptop and paperwork"></div>
<div class="abs tools-panel"></div>
<h2 class="abs tools-title">TOOLS &amp; BENEFITS</h2>

<div class="abs tool" style="top:1228px"><span class="ring"><svg width="28" height="22" viewBox="0 0 28 22"><rect x="5" y="2" width="18" height="13" rx="1" fill="none" stroke="#fff" stroke-width="2"/><path d="M1 18h26v2H1z" fill="#fff"/></svg></span>Online Loan Application</div>
<div class="abs tool" style="top:1316px"><span class="ring"><svg width="26" height="24" viewBox="0 0 26 24"><path d="M1 10h11V5l8 7-8 7v-5H1z" fill="#fff"/><path d="M15 2h8v20h-8" fill="none" stroke="#fff" stroke-width="2.5"/></svg></span>Internet Teller Sign Up Form</div>
<div class="abs tool" style="top:1404px"><span class="ring"><svg width="28" height="26" viewBox="0 0 28 26"><circle cx="10" cy="15" r="6" fill="none" stroke="#fff" stroke-width="4" stroke-dasharray="3 2"/><circle cx="10" cy="15" r="2" fill="#fff"/><circle cx="21" cy="7" r="4" fill="none" stroke="#fff" stroke-width="3" stroke-dasharray="2 1.5"/><circle cx="21" cy="20" r="3.5" fill="none" stroke="#fff" stroke-width="3" stroke-dasharray="2 1.5"/></svg></span>Member Services Benefits</div>
<div class="abs tool" style="top:1492px"><span class="ring"><svg width="22" height="28" viewBox="0 0 22 28"><rect x="1" y="1" width="20" height="26" rx="2" fill="none" stroke="#fff" stroke-width="2"/><rect x="4" y="4" width="14" height="5" fill="#fff"/><g fill="#fff"><rect x="4" y="12" width="3.5" height="3"/><rect x="9.2" y="12" width="3.5" height="3"/><rect x="14.5" y="12" width="3.5" height="3"/><rect x="4" y="17" width="3.5" height="3"/><rect x="9.2" y="17" width="3.5" height="3"/><rect x="14.5" y="17" width="3.5" height="3"/><rect x="4" y="22" width="3.5" height="3"/><rect x="9.2" y="22" width="3.5" height="3"/><rect x="14.5" y="22" width="3.5" height="3"/></g></svg></span>Financial Calculators</div>

<!-- products & services -->
<h2 class="abs section-title products-title">PRODUCTS &amp; SERVICES</h2>

<article class="abs product" style="left:100px">
  <div class="photo" role="img" aria-label="Photograph of a couple meeting a loan advisor in a bright office" style="background:linear-gradient(135deg,#e8e6e2,#b9b3ab 50%,#6d6a68)"></div>
  <h4>LOAN PRODUCTS</h4>
  <p>At Pinewood &amp; Harbour Growers Cooperative Credit Union Limited we focus on building relationships with our members that last.</p>
  <span class="more">READ MORE &gt;&gt;</span>
</article>

<article class="abs product" style="left:443px">
  <div class="photo" role="img" aria-label="Photograph of hands holding a smartphone showing a credit score in front of a laptop" style="background:linear-gradient(135deg,#8fb5d6,#d9dee3 45%,#6f7378)"></div>
  <h4>LOANS BY PHONE</h4>
  <p>At Pinewood &amp; Harbour Growers Cooperative Credit Union Limited we focus on building relationships with our members that last.</p>
  <span class="more">READ MORE &gt;&gt;</span>
</article>

<article class="abs product" style="left:786px">
  <div class="photo" role="img" aria-label="Photograph of a fanned stack of bank cards on a grey surface" style="background:linear-gradient(135deg,#8c8e90,#5e6166 45%,#c9a957 70%,#7a7c80)"></div>
  <h4>ATM CARDS RENEWAL</h4>
  <p>At Pinewood &amp; Harbour Growers Cooperative Credit Union Limited we focus on building relationships with our members that last.</p>
  <span class="more">READ MORE &gt;&gt;</span>
</article>

<!-- news & featured rates -->
<div class="abs news-band"></div>
<div class="abs news-photo" role="img" aria-label="Photograph of a smiling couple reviewing finances together at home"></div>
<h2 class="abs news-title">NEWS &amp; EVENTS</h2>
<div class="abs news-head">Sit voluptatem accusantium dolore lauda</div>
<div class="abs news-meta">
  <svg width="11" height="11" viewBox="0 0 11 11"><rect x="0" y="1" width="11" height="10" fill="#6b449b"/><rect x="1.5" y="4" width="8" height="5.5" fill="#fff"/></svg>09/03/2017<span class="sep">|</span>
  <svg width="10" height="11" viewBox="0 0 10 11"><circle cx="5" cy="3" r="2.8" fill="#6b449b"/><path d="M0 11c0-4 2-5.5 5-5.5s5 1.5 5 5.5z" fill="#6b449b"/></svg>Ren Calloway<span class="sep">|</span>
  <svg width="12" height="11" viewBox="0 0 12 11"><path d="M1 1h10v7H5l-3 3V8H1z" fill="none" stroke="#6b449b" stroke-width="1.5"/></svg>0 Comments
</div>
<p class="abs news-text">Nemo enim ipsam voluptatem quia voluptas sit aspernatur aut odit aut fugit, sed quia consequuntur magni dolores.</p>
<div class="abs news-more">READ MORE &gt;&gt;</div>
<div class="abs arrows">
  <span><svg width="8" height="10" viewBox="0 0 8 10"><path d="M6 1L2 5l4 4" fill="none" stroke="#fff" stroke-width="2"/></svg></span>
  <span><svg width="8" height="10" viewBox="0 0 8 10"><path d="M2 1l4 4-4 4" fill="none" stroke="#fff" stroke-width="2"/></svg></span>
</div>

<aside class="abs rates">
  <h2>FEATURED RATES</h2>
  <div class="rate" style="top:96px">Consumer Loans<b>9.00% <small>APR*</small></b></div>
  <div class="rate" style="top:134px">New Auto/Motorcycle<b>7.00% <small>APR*</small></b></div>
  <div class="rate" style="top:172px">Used Auto/Motorcycle<b>11.75% <small>APR*</small></b></div>
  <div class="rate" style="top:211px">Mortgages<b>8.25% <small>APR*</small></b></div>
  <div class="note">*APR - Annual Percentage Rate.<strong>APPLY FOR A LOAN &gt;</strong></div>
</aside>

<!-- footer -->
<div class="abs contacts">
  <div class="item"><span class="ring"><svg width="18" height="18" viewBox="0 0 24 24"><path fill="#f37122" d="M6.6 10.8a15 15 0 006.6 6.6l2.2-2.2c.3-.3.7-.4 1-.2 1.1.4 2.3.6 3.6.6.6 0 1 .4 1 1V20c0 .6-.4 1-1 1A17 17 0 013 4c0-.6.4-1 1-1h3.5c.6 0 1 .4 1 1 0 1.3.2 2.5.6 3.6.1.3 0 .7-.2 1z"/></svg></span>(555) 310-4827</div>
  <div class="item"><span class="ring"><svg width="18" height="18" viewBox="0 0 24 24"><path fill="#f37122" d="M4 8h16v9h-3v4H7v-4H4zM7 3h10v4H7zm2 12v4h6v-4z"/></svg></span>(555) 310-6158</div>
</div>
<nav class="abs footer-nav">Home<span>|</span>About Us<span>|</span>Product &amp; Services<span>|</span>Tools &amp; Benefits<span>|</span>News<span>|</span>Contact Us</nav>
<div class="abs rule"></div>
<div class="abs copyright">Copyrights © 2017, PHFC. All right reserved.</div>
<div class="abs social" aria-label="Social media links"><span></span><span></span><span></span><span></span></div>

</body>
</html>
```